professional business card design for technology company

We are a small technology consulting firm, specialising in consulting based around Cloud and Managed services. Our colour scheme is yellow, blue and white, as you can see in the logos. Although we are based in melbourne australia, due to the nature of our work, our clients can be located anywhere. We are looking for a clean, professional, positive look - similar to our company logo

Target Market(s)

small business

Industry/Entity Type

Business

Contact Information for Business Card

eye catching, designed to incorporate some level of raised printing. Must contain website address, phone number, name and job title

Requirements
Must have
• Logo (attached) - use of the same colour scheme

```html
<!DOCTYPE html>
<html lang="en">
<head>
<meta charset="utf-8">
<title>Nimbara – Business Card</title>
<link rel="stylesheet" href="https://fonts.googleapis.com/css2?family=Open+Sans:wght@300;400;700&display=swap">
<style>
  :root {
    --stage: #d8dbde;
    --card-light: #ffffff;
    --card-shade: #e4e5e7;
    --panel-grey: #5e5e5f;
    --accent-blue: #39ade3;
    --brand-grey: #58595b;
    --ink-white: #ffffff;
  }
  * { margin: 0; padding: 0; box-sizing: border-box; }
  html, body {
    width: 1200px;
    height: 865px;
    overflow: hidden;
    background: var(--stage);
    font-family: "Open Sans", Arial, sans-serif;
  }
  .canvas {
    position: relative;
    width: 1200px;
    height: 865px;
  }
  .business-card {
    position: absolute;
    left: 100px;
    top: 146px;
    width: 1000px;
    height: 572px;
    overflow: hidden;
    box-shadow: 0 10px 30px rgba(0,0,0,0.18);
  }
  .card-shapes {
    position: absolute;
    inset: 0;
    width: 1000px;
    height: 572px;
  }
  .brand {
    position: absolute;
    left: 70px;
    top: 250px;
    display: flex;
    align-items: center;
    gap: 22px;
  }
  .brand-dot {
    width: 46px;
    height: 46px;
    border-radius: 50%;
    background: var(--accent-blue);
  }
  .brand-name {
    font-weight: 700;
    font-size: 92px;
    letter-spacing: -3px;
    color: var(--brand-grey);
    line-height: 1;
  }
  .contact-block {
    position: absolute;
    right: 46px;
    top: 48px;
    text-align: right;
    color: var(--ink-white);
  }
  .person-name {
    font-weight: 700;
    font-size: 28px;
    line-height: 1.2;
  }
  .person-title {
    font-weight: 300;
    font-size: 25px;
    line-height: 1.2;
    margin-bottom: 50px;
  }
  .contact-line {
    font-weight: 400;
    font-size: 22px;
    line-height: 1.42;
    display: flex;
    justify-content: flex-end;
    align-items: center;
    gap: 8px;
  }
  .contact-icon {
    width: 18px;
    height: 18px;
    fill: var(--ink-white);
  }
  .gap-before { margin-top: 8px; }
</style>
</head>
<body>
<main class="canvas">
  <section class="business-card">
    <svg class="card-shapes" viewBox="0 0 1000 572" aria-hidden="true">
      <defs>
        <linearGradient id="card-light-fill" x1="0" y1="0" x2="0.6" y2="1">
          <stop offset="0" stop-color="var(--card-light)"/>
          <stop offset="1" stop-color="var(--card-shade)"/>
        </linearGradient>
      </defs>
      <rect class="panel-grey" width="1000" height="572" fill="var(--panel-grey)"/>
      <path class="divider-line" d="M380,0 C540,30 700,200 712,572 H0 V0 Z" fill="#ffffff"/>
      <path class="accent-crescent" d="M560,110 C650,220 700,380 700,572 H530 C590,400 600,250 560,110 Z" fill="var(--accent-blue)"/>
      <path class="light-bulge" d="M0,0 H380 C480,20 540,60 560,110 C600,250 590,400 530,572 H0 Z" fill="url(#card-light-fill)"/>
    </svg>

    <div class="brand">
      <span class="brand-dot"></span>
      <span class="brand-name">Nimbara</span>
    </div>

    <div class="contact-block">
      <p class="person-name">Maren Calloway</p>
      <p class="person-title">Consultant</p>
      <p class="contact-line">214 9th floor,Quay</p>
      <p class="contact-line">Harbour Lane MTR</p>
      <p class="contact-line gap-before">013 456 7890
        <svg class="contact-icon" viewBox="0 0 24 24" aria-label="phone"><path d="M6.6 10.8a15.1 15.1 0 0 0 6.6 6.6l2.2-2.2c.3-.3.7-.4 1-.2 1.1.4 2.3.6 3.6.6.6 0 1 .4 1 1V20c0 .6-.4 1-1 1A17 17 0 0 1 3 4c0-.6.4-1 1-1h3.5c.6 0 1 .4 1 1 0 1.3.2 2.5.6 3.6.1.3 0 .7-.2 1z"/></svg>
      </p>
      <p class="contact-line">013 456 7891
        <svg class="contact-icon" viewBox="0 0 24 24" aria-label="fax"><path d="M7 2h8l3 3v5H7z M4 11h16v10H4z M7 14h2v2H7z M11 14h2v2h-2z M15 14h2v2h-2z M7 18h10v1H7z"/></svg>
      </p>
      <p class="contact-line">maren@nimbara.com
        <svg class="contact-icon" viewBox="0 0 24 24" aria-label="email"><path d="M2 5h20v14H2z M3.5 6.5 12 13l8.5-6.5" stroke="#5e5e5f" stroke-width="1.4"/></svg>
      </p>
      <p class="contact-line">www.nimbaracloud.com</p>
    </div>
  </section>
</main>
</body>
</html>
```